ULMIRA card Technical Architecture

Hello everyone ULMIRA: It is a consulting firm in Architecture and Construction. I require a card duplexing, sober, elegant, classic but not boring. Update 1: Use the following data for the card. Name: Gonzalo Pereda Mauricio Villalta Position: COO Twitter: @ulmiraAT Homepage: ulmira-example.com home address not include the participation of all thank you.

Target Market(s)

Construction companies, Architects and Consulting Engineers

Industry/Entity Type

Consulting

Contact Information for Business Card

Los campos que debe tener:
Nombre, Cargo, email, homepage y twitter

Font styles to use
Serif
Sans Serif
Other font styles liked:
• Me gustan playfair display, open sans y roboto, pero estoy sujeto a sus propuestas

Requirements
Must have
• Colors: Present combined proposals in white, red, gray and black Update 1: The two names must be clearly differentiated from the two surnames
Nice to have
• They are free to present their best proposals. I will bring them immediate feedback to the extent you can go see their designs. Complete data for card and logo files will give the winner the

```html
<!DOCTYPE html>
<html lang="es">
<head>
<meta charset="utf-8">
<title>ULMIRA – Tarjeta de presentación</title>
<link href="https://fonts.googleapis.com/css2?family=Josefin+Sans:wght@300;400&family=Open+Sans:wght@400;600&display=swap" rel="stylesheet">
<style>
  :root {
    --stage: #3a3a3c;
    --paper: #ffffff;
    --ink: #2b2b2d;
    --ink-soft: #6b6b6e;
    --red: #c0141c;
    --red-deep: #6e0208;
    --red-mid: #a20c13;
    --black: #0d0d0e;
    --white: #ffffff;
    --grey-light: #d9d9db;
  }
  * { box-sizing: border-box; margin: 0; padding: 0; }
  html, body {
    width: 1200px; height: 843px; overflow: hidden;
    background: var(--stage);
  }
  .canvas {
    position: relative; width: 1200px; height: 843px;
  }
  .card {
    position: absolute; width: 530px; height: 309px;
    overflow: hidden; border-radius: 3px;
    box-shadow: 0 10px 28px rgba(0,0,0,.45);
  }

  /* Back side */
  .card-back {
    left: 40px; top: 267px;
    background: radial-gradient(ellipse at 45% 30%, var(--red) 0%, var(--red-mid) 45%, var(--red-deep) 100%);
    display: flex; flex-direction: column; align-items: center; justify-content: center;
    color: var(--white);
  }
  .brand-name {
    font-family: "Josefin Sans", sans-serif; font-weight: 300;
    letter-spacing: 0.42em; font-size: 46px; line-height: 1;
    padding-left: 0.42em;
  }
  .brand-rule { width: 300px; height: 1px; margin: 12px 0 8px; }
  .card-back .brand-rule { background: rgba(255,255,255,.75); }
  .brand-tagline {
    font-family: "Josefin Sans", sans-serif; font-weight: 400;
    letter-spacing: 0.22em; font-size: 16px; text-transform: uppercase;
  }
  .brand-mark {
    width: 18px; height: 18px; border-radius: 50%; margin-bottom: 18px;
  }
  .card-back .brand-mark { background: var(--white); }
  .website {
    margin-top: 26px;
    font-family: "Open Sans", sans-serif; font-size: 12px; letter-spacing: 0.18em;
  }

  /* Front side */
  .card-front {
    left: 630px; top: 267px;
    background: linear-gradient(180deg, var(--paper) 0%, #f3f3f4 100%);
  }
  .card-front .swoosh { position: absolute; inset: 0; }
  .front-brand {
    position: absolute; left: 40px; top: 44px; width: 320px;
    display: flex; flex-direction: column; align-items: flex-start;
  }
  .front-brand .brand-mark { background: var(--red); margin: 0 0 14px 150px; }
  .front-brand .brand-name { color: var(--ink); font-size: 44px; padding-left: 0; }
  .front-brand .brand-rule { background: var(--red); width: 310px; margin: 8px 0 6px; }
  .front-brand .brand-tagline { color: var(--red); font-size: 15px; }

  .contact {
    position: absolute; right: 28px; top: 176px;
    text-align: right; font-family: "Open Sans", sans-serif;
    color: var(--grey-light);
  }
  .contact-name { color: var(--red); font-size: 17px; font-weight: 400; line-height: 1.2; }
  .contact-role { color: var(--white); font-size: 15px; line-height: 1.2; margin-bottom: 12px; }
  .contact-line {
    display: flex; justify-content: flex-end; align-items: center; gap: 8px;
    font-size: 14px; line-height: 1.35;
  }
  .contact-icon { width: 13px; height: 13px; flex: none; }
</style>
</head>
<body>
<main class="canvas">

  <section class="card card-back" aria-label="Reverso de la tarjeta">
    <span class="brand-mark" aria-hidden="true"></span>
    <div class="brand-name">ULMIRA</div>
    <div class="brand-rule"></div>
    <div class="brand-tagline">Arquitectura Técnica</div>
    <div class="website">www.ulmira-example.com</div>
  </section>

  <section class="card card-front" aria-label="Anverso de la tarjeta">
    <svg class="swoosh" viewBox="0 0 530 309" preserveAspectRatio="none" aria-hidden="true">
      <defs>
        <linearGradient id="panel-fill" x1="0" y1="0" x2="1" y2="1">
          <stop offset="0" stop-color="#2a2a2c"/>
          <stop offset="0.5" stop-color="#0d0d0e"/>
          <stop offset="1" stop-color="#000"/>
        </linearGradient>
      </defs>
      <path d="M196 309 C 270 200, 390 140, 530 112 L 530 309 Z" fill="url(#panel-fill)"/>
      <path d="M180 309 C 258 190, 380 126, 530 96" fill="none" stroke="#8e0a10" stroke-width="7"/>
      <path d="M188 309 C 264 196, 384 134, 530 104" fill="none" stroke="#c0141c" stroke-width="4"/>
      <path d="M170 309 C 250 182, 374 118, 530 86" fill="none" stroke="#b01018" stroke-width="2.5"/>
    </svg>

    <div class="front-brand">
      <span class="brand-mark" aria-hidden="true"></span>
      <div class="brand-name">ULMIRA</div>
      <div class="brand-rule"></div>
      <div class="brand-tagline">Arquitectura Técnica</div>
    </div>

    <div class="contact">
      <div class="contact-name">Gonzalo Pereda</div>
      <div class="contact-role">COO</div>
      <div class="contact-line">555 0147 2208
        <svg class="contact-icon" viewBox="0 0 16 16" aria-hidden="true"><path fill="#c0141c" d="M3.6 1.5l2.3 2.6-1.3 1.8c.8 1.9 2.3 3.4 4.2 4.3l1.8-1.3 2.6 2.3-1.3 2.3C7 13.5 2.5 9 1.3 3z"/></svg>
      </div>
      <div class="contact-line">mail@ulmira-example.com
        <svg class="contact-icon" viewBox="0 0 16 16" aria-hidden="true"><rect x="1" y="3" width="14" height="10" fill="#c0141c"/><path d="M1 3l7 6 7-6" fill="none" stroke="#0d0d0e" stroke-width="1.3"/></svg>
      </div>
      <div class="contact-line">@ulmiraAT
        <svg class="contact-icon" viewBox="0 0 16 16" aria-hidden="true"><circle cx="8" cy="8" r="6" fill="#c0141c"/></svg>
      </div>
    </div>
  </section>

</main>
</body>
</html>
```